Baby Boutique Needs a Business Card Design

We need a modern double sided business card design using the attached logo for Little Wren Nook.

Little Wren Nook is a baby boutique which sells only handmade clothing and accessories for both boys and girls. Our store will live exclusively online.

We would like to only use the colors that have been used in the logo.

Target Market(s)

Potential wholesale clients, Small business owners

Industry/Entity Type

Retail

Contact Information for Business Card

Name Gideon R. Falkner (Owner)
Email sales@littlewrennook.example
Main Phone 555-203-7719
Cell phone 555-203-7746
Website www.LittleWrenNook.example

Font styles to use
Sans Serif

Colors

Designer to choose colors to be used in the design.

Requirements
Must have
• -Would like to have icons that indentify the contact information.
• -Include our website
• -Include our tagline in a small area near the bottom. "Handmade Baby Creations"
• -Would like to include Facebook and Instagram Icons
• -
Nice to have
• Would like to have a simple back side with the logo.
• Something along the lines of the meadowfield lending card attached.

```html
<!DOCTYPE html>
<html lang="en">
<head>
<meta charset="utf-8">
<title>Little Wren Nook — Business Card</title>
<link rel="stylesheet" href="https://fonts.googleapis.com/css2?family=Oswald:wght@500&family=Work+Sans:wght@400;600&display=swap">
<style>
  :root {
    --stage: #e9e6e3;
    --card: #1d1c1e;
    --teal: #7fd6c6;
    --coral: #e6605f;
    --band-text: #f6e9e8;
  }
  * { box-sizing: border-box; margin: 0; padding: 0; }
  html, body {
    width: 1200px; height: 715px; overflow: hidden;
    background: var(--stage);
    font-family: "Work Sans", sans-serif;
  }
  .sheet {
    position: relative; width: 1200px; height: 715px;
    display: flex; align-items: center; justify-content: center; gap: 60px;
  }
  .card {
    position: relative; width: 500px; height: 286px;
    background: var(--card); border-radius: 8px; overflow: hidden;
    box-shadow: 0 6px 18px rgba(0,0,0,.18);
  }
  /* Front */
  .card--front { display: flex; align-items: center; justify-content: center; }
  .brand-name {
    font-family: "Work Sans", sans-serif; font-weight: 600;
    font-size: 36px; color: var(--teal); letter-spacing: .5px;
  }
  /* Back */
  .identity {
    position: absolute; right: 262px; top: 92px; text-align: right;
  }
  .identity__name {
    font-family: "Oswald", sans-serif; font-weight: 500;
    font-size: 25px; line-height: 1; color: var(--coral);
    text-transform: uppercase; letter-spacing: .3px; white-space: nowrap;
  }
  .identity__role { margin-top: 6px; font-size: 13px; color: var(--teal); }
  .divider {
    position: absolute; left: 256px; top: 92px; width: 2px; height: 70px;
    background: var(--teal);
  }
  .contacts {
    position: absolute; left: 272px; top: 96px; list-style: none;
  }
  .contacts li {
    display: flex; align-items: center; gap: 7px;
    font-size: 12px; line-height: 16.5px; color: var(--teal); white-space: nowrap;
  }
  .contacts svg { width: 9px; height: 9px; flex: none; }
  .social {
    position: absolute; right: 34px; bottom: 52px; display: flex; gap: 10px;
  }
  .social span {
    width: 17px; height: 17px; border: 2px solid var(--coral); border-radius: 4px;
  }
  .rule {
    position: absolute; left: 0; right: 0; bottom: 31px; height: 2px;
    background: var(--teal);
  }
  .tagline-band {
    position: absolute; left: 0; right: 0; bottom: 0; height: 28px;
    background: var(--coral); display: flex; align-items: center; padding-left: 70px;
  }
  .tagline { font-size: 13px; color: var(--band-text); letter-spacing: .4px; }
</style>
</head>
<body>
<main class="sheet">
  <section class="card card--front" aria-label="Card front">
    <h1 class="brand-name">Little Wren Nook</h1>
  </section>

  <section class="card card--back" aria-label="Card back">
    <div class="identity">
      <p class="identity__name">Gideon R. Falkner</p>
      <p class="identity__role">Owner</p>
    </div>
    <div class="divider"></div>
    <ul class="contacts">
      <li>
        <svg viewBox="0 0 10 10" aria-hidden="true"><path d="M2 1l2 2-1 1.2c.6 1.2 1.5 2.1 2.8 2.8L7 6l2 2-1.2 1.2C4.5 8.6 1.4 5.5.8 2.2z" fill="var(--coral)"/></svg>
        555-203-7719
      </li>
      <li>
        <svg viewBox="0 0 10 10" aria-hidden="true"><rect x="2.5" y=".5" width="5" height="9" rx="1" fill="none" stroke="var(--coral)" stroke-width="1.2"/><circle cx="5" cy="7.8" r=".6" fill="var(--coral)"/></svg>
        555-203-7746
      </li>
      <li>
        <svg viewBox="0 0 10 10" aria-hidden="true"><rect x=".6" y="2" width="8.8" height="6" fill="none" stroke="var(--coral)" stroke-width="1.2"/><path d="M.8 2.3L5 5.5l4.2-3.2" fill="none" stroke="var(--coral)" stroke-width="1.1"/></svg>
        sales@littlewrennook.example
      </li>
      <li>
        <svg viewBox="0 0 10 10" aria-hidden="true"><circle cx="5" cy="5" r="4.2" fill="none" stroke="var(--coral)" stroke-width="1.1"/><ellipse cx="5" cy="5" rx="1.8" ry="4.2" fill="none" stroke="var(--coral)" stroke-width=".9"/><path d="M.8 5h8.4" stroke="var(--coral)" stroke-width=".9"/></svg>
        www.LittleWrenNook.example
      </li>
    </ul>
    <div class="social">
      <span role="img" aria-label="Social profile"></span>
      <span role="img" aria-label="Social profile"></span>
    </div>
    <div class="rule"></div>
    <div class="tagline-band"><p class="tagline">Handmade Baby Creations</p></div>
  </section>
</main>
</body>
</html>
```